Lantern Petals Website v.1 - attract floral shop franchisees

I need a simple information website for my new business. We are a franchisor of flower shops. The overall purpose of the website is to promote the company and the service, especially to potential franchisees and retailers. Only about 4 pages are required including homepage, About, For Supermarkets, For Franchisees, and Contact. No special functions are required except the site will have two separate inquiry forms that must be filled out online and submitted via automated email. Similarly, an email form should be linked from the Contact page. I have a logo and business cards designed by ArtMingle, and I would like the site to have a consistent color scheme and style. The key to design will be to express the joy and love associated with flowers and floral bouquets.
IMPORTANT - I will be exporting the website design to Wordpress CMS in a site hosted by HostNimbus. For smooth integration into WordPress hosted by HostNimbus, the designer should build the site using a WordPress-friendly format. Ideally, they should use HTML, CSS, and PHP. Creating a custom theme or using a page builder that exports to WordPress-compatible files is best. This ensures the site can be easily imported and managed within WordPress.

Target Market(s)

Potential franchisees (existing florists or creative types who might like to own a floral business) and supermarkets who might want us to run their floral department

Industry/Entity Type

Floral retailing

Requirements
Must have
• A brand theme that is beautiful, consistent throughout and builds on the logo design
Nice to have
• Show gender and ethnic diversity in customers and florists. Pictures of happy florists (for franchisees) and pictures of amazing floral department displays (for supermarkets)

```html
<!DOCTYPE html>
<html lang="en">
<head>
<meta charset="utf-8">
<title>Lantern Petals – Website Pages</title>
<link href="https://fonts.googleapis.com/css2?family=Domine:wght@700&family=Roboto:wght@400;500;700&display=swap" rel="stylesheet">
<style>
:root{
  --orange:#f29b17;
  --green:#129a4a;
  --black:#050505;
  --ink:#222;
  --muted:#666;
  --canvas:#e4e4e4;
  --white:#fff;
}
*{box-sizing:border-box;margin:0;padding:0}
html,body{width:1200px;height:825px;overflow:hidden;background:var(--canvas);font-family:"Roboto",Arial,sans-serif;color:var(--ink)}
.stage{position:absolute;left:0;top:0;width:2321px;height:1596px;transform:scale(.51702);transform-origin:0 0}
.page{position:absolute;top:102px;width:473px;background:var(--white);overflow:hidden;box-shadow:0 1px 4px rgba(0,0,0,.08)}
.page--home{left:110px;height:1391px}
.page--about{left:652px;height:1022px}
.page--markets{left:1195px;height:1058px}
.page--franchise{left:1738px;height:1126px}

/* header */
.topbar{position:absolute;left:0;top:0;width:100%;height:42px;background:var(--white);z-index:3}
.brand{position:absolute;left:43px;top:12px;display:flex;align-items:center;gap:4px;font-family:"Domine",Georgia,serif;font-weight:700;font-size:11px;color:var(--orange);white-space:nowrap}
.brand__dot{width:12px;height:12px;border-radius:50%;background:var(--green)}
.social{position:absolute;top:6px;width:13px;height:13px;border-radius:50%;border:1.2px solid var(--green)}
.social--a{left:325px}.social--b{left:344px}
.call{position:absolute;left:364px;top:6px;display:flex;gap:4px;align-items:center}
.call__icon{width:13px;height:13px;border-radius:50%;background:var(--orange);display:flex;align-items:center;justify-content:center}
.call__text{font-size:4.5px;line-height:1.3;color:var(--muted)}
.call__text b{display:block;font-size:5.5px;color:var(--ink)}
.nav{position:absolute;left:190px;top:28px;display:flex;gap:15px;font-size:5.2px;font-weight:500;letter-spacing:.2px;color:#333}

/* hero */
.hero{position:absolute;left:0;top:42px;width:100%;height:285px}
.hero--home{background:linear-gradient(120deg,#c23a6d 0%,#e6a0a8 30%,#d8b79a 55%,#5f8b4e 80%,#a43468 100%)}
.hero--about{background:linear-gradient(120deg,#3a3a3a 0%,#6d6a66 35%,#f0d9d4 55%,#c7a2a0 75%,#3b3b3b 100%)}
.hero--markets{background:linear-gradient(120deg,#6f8a66 0%,#c9c0b5 35%,#e8c3c6 60%,#8e9a7a 100%)}
.hero--franchise{background:linear-gradient(120deg,#5a7c7c 0%,#9a86c9 40%,#e8dfe2 65%,#c3b7a5 100%)}
.hero__shade{position:absolute;inset:0;background:rgba(0,0,0,.28)}
.hero__title{position:absolute;left:0;width:100%;text-align:center;font-family:"Domine",Georgia,serif;font-weight:700;color:var(--white);text-shadow:0 1px 3px rgba(0,0,0,.35)}
.hero__kicker{top:100px;font-size:14px}
.hero__main{top:122px;font-size:25px}
.hero__single{top:122px;font-size:25px}
.hero__btn{position:absolute;left:203px;top:172px}
.wave{position:absolute;left:0;width:473px;z-index:2}
.wave--hero{top:238px;height:105px}

/* common type */
.h2{position:absolute;font-family:"Domine",Georgia,serif;font-weight:700;font-size:15px;color:var(--ink)}
.h2--center{left:0;width:100%;text-align:center}
.copy{position:absolute;font-size:5.2px;line-height:1.75;color:var(--muted);text-align:justify}
.copy p+p{margin-top:6px}
.copy--center{text-align:center}
.btn{position:absolute;display:inline-flex;align-items:center;gap:4px;height:16px;padding:0 9px;border-radius:9px;background:var(--orange);color:var(--white);font-size:4.8px;font-weight:700;letter-spacing:.3px;white-space:nowrap}
.btn__arrow{width:6px;height:6px;border-radius:50%;background:var(--white)}
.btn--ghost{background:transparent;border:1px solid var(--white)}
.photo{position:absolute}
.frame{position:absolute;border:1.5px solid var(--green)}
.hex{position:absolute;clip-path:polygon(50% 0,100% 25%,100% 75%,50% 100%,0 75%,0 25%)}
.list{position:absolute;list-style:none;font-size:5px;line-height:1.45;color:#333}
.list li{position:relative;padding-left:13px;margin-bottom:6px}
.list li::before{content:"";position:absolute;left:0;top:1px;width:6px;height:6px;border-radius:50%;border:1.6px dotted var(--orange)}

/* contact band */
.contact-band{position:absolute;left:0;top:792px;width:100%;height:126px;background:var(--green);color:var(--white);text-align:center}
.contact-band .h2{color:var(--white);top:20px}
.contact-band__text{position:absolute;left:85px;width:303px;top:46px;font-size:5px;line-height:1.8}
.contact-band .btn--one{left:94px;top:85px}
.contact-band .btn--two{left:229px;top:85px}

/* footer */
.footer{position:absolute;left:0;bottom:0;width:100%;height:230px}
.footer__wave{position:absolute;left:0;top:0;width:473px;height:80px}
.footer__body{position:absolute;left:0;top:78px;width:100%;height:133px;background:var(--black);color:var(--white)}
.footer__brand{position:absolute;left:45px;top:28px;display:flex;align-items:center;gap:4px;font-family:"Domine",Georgia,serif;font-weight:700;font-size:12px;color:var(--orange)}
.footer__col{position:absolute;top:12px;font-size:4.6px;line-height:1.4}
.footer__col h4{font-size:4.8px;font-weight:700;letter-spacing:.2px;margin-bottom:4px}
.footer__col h4::after{content:"";display:block;width:14px;height:1px;background:var(--white);margin-top:4px}
.footer__col--links{left:147px}
.footer__col--contact{left:227px}
.footer__col--news{left:328px;width:105px}
.footer__col ul{list-style:none}
.footer__col--links li{margin-bottom:5px;padding-left:10px;position:relative}
.footer__col--links li::before{content:"»";position:absolute;left:0}
.footer__col--contact li{display:flex;gap:6px;align-items:flex-start;margin-bottom:6px}
.ic{flex:none;width:7px;height:7px;border-radius:50%;background:#333}
.footer__phone{font-weight:700;font-size:5.4px}
.footer__loc{text-decoration:underline}
.signup{display:flex;align-items:center;margin-top:6px;width:100px;height:16px;border-radius:9px;background:var(--white);color:#999;padding-left:10px;font-size:4.4px;position:relative}
.signup__go{position:absolute;right:0;top:0;width:16px;height:16px;border-radius:50%;background:var(--green)}
.footer__social{display:flex;gap:4px;margin-top:8px}
.footer__social span{width:10px;height:10px;border-radius:50%;background:var(--white)}
.footer__bar{position:absolute;left:0;bottom:0;width:100%;height:19px;background:var(--orange);color:var(--white);font-size:4.6px;display:flex;align-items:center;justify-content:center}
</style>
</head>
<body>
<div class="stage">

<!-- ================= HOME ================= -->
<section class="page page--home">
  <header class="topbar">
    <div class="brand"><span class="brand__dot"></span>Lantern Petals</div>
    <span class="social social--a"></span><span class="social social--b"></span>
    <div class="call"><span class="call__icon"><svg width="7" height="7" viewBox="0 0 24 24"><path fill="#fff" d="M6.6 10.8a15 15 0 0 0 6.6 6.6l2.2-2.2c.3-.3.7-.4 1-.2 1.1.4 2.3.6 3.6.6.6 0 1 .4 1 1V20c0 .6-.4 1-1 1A17 17 0 0 1 3 4c0-.6.4-1 1-1h3.5c.6 0 1 .4 1 1 0 1.3.2 2.5.6 3.6.1.3 0 .7-.2 1z"/></svg></span><div class="call__text">Call Us<b>+ 1.555.010.2040</b></div></div>
    <nav class="nav"><span>HOME</span><span>ABOUT</span><span>FOR SUPERMARKETS</span><span>FOR FRANCHISEES</span><span>CONTACT</span></nav>
  </header>
  <div class="hero hero--home" role="img" aria-label="Smiling florist arranging colourful flowers in her shop">
    <div class="hero__shade"></div>
    <div class="hero__title hero__kicker">Welcome To</div>
    <div class="hero__title hero__main">Lantern Petals</div>
    <span class="btn hero__btn">GET STARTED <span class="btn__arrow"></span></span>
  </div>
  <svg class="wave wave--hero" viewBox="0 0 473 105" preserveAspectRatio="none"><path fill="#f29b17" d="M0 46C120 -2 260 84 473 16V105H0Z"/><path fill="#129a4a" d="M0 60C120 12 260 98 473 30V105H0Z"/><path fill="#fff" d="M0 68C120 20 260 106 473 38V105H0Z"/></svg>

  <h2 class="h2" style="left:43px;top:398px">About Us</h2>
  <div class="copy" style="left:43px;top:422px;width:162px">Lantern Petals operates in partnership with Bluegale Group, the leading franchisor of sushi stations and pre-packaged fruit &amp; vegetable departments to supermarkets across the United States and United Kingdom. Lantern Petals’ combination of floral and supermarket franchising expertise guarantees that consumers, franchisees and supermarket partners each receive exceptional service and value.</div>
  <span class="btn" style="left:43px;top:514px">LEARN MORE <span class="btn__arrow"></span></span>
  <div class="photo" style="left:277px;top:386px;width:153px;height:146px;background:linear-gradient(135deg,#8b6a4f,#c6a184 45%,#4f6f52)" role="img" aria-label="Florists working together at a flower counter"></div>
  <div class="photo" style="left:241px;top:449px;width:95px;height:100px;border:3px solid #fff;background:linear-gradient(135deg,#d24f86,#f1a7c3 50%,#6f9a55)" role="img" aria-label="Pink gift box filled with roses"></div>

  <div class="photo" style="left:0;top:590px;width:245px;height:202px;background:linear-gradient(135deg,#eee6d8,#f2b2b9 45%,#8cae62 75%,#e8e0c8)" role="img" aria-label="Hands holding a large mixed bouquet"></div>
  <div style="position:absolute;left:245px;top:590px;width:228px;height:202px;background:#f4f4f4"></div>
  <svg style="position:absolute;left:220px;top:590px" width="30" height="202"><path d="M28 0 L2 202" stroke="#f29b17" stroke-width="2"/></svg>
  <h2 class="h2" style="left:262px;top:613px">For Supermarkets</h2>
  <div class="copy" style="left:262px;top:637px;width:168px"><p>Lantern Petals works with some of the country’s largest and most progressive supermarkets to provide franchisee ownership and operation of their strategically important floral departments. Supermarkets find that Lantern Petals is able to improve their financial outcomes, provide attentive customer service and satisfaction, and lift the quality of the entire store environment.</p><p>Lantern Petals works with some of the country’s largest and most progressive supermarkets to provide franchisee ownership and operation of their strategically important floral departments.</p></div>
  <span class="btn" style="left:262px;top:757px">LEARN MORE <span class="btn__arrow"></span></span>

  <div class="contact-band">
    <h2 class="h2 h2--center">Contact Us</h2>
    <p class="contact-band__text">Get in touch to learn how our floral franchise model works for florists, creative owners and supermarket partners. Send us a short note and our team will reply with next steps, support details and local openings near you soon.</p>
    <span class="btn btn--one">NEW FLORIST FRANCHISE INQUIRY <span class="btn__arrow"></span></span>
    <span class="btn btn--ghost btn--two">PROFESSIONAL FLORIST FRANCHISE INQUIRY <span class="btn__arrow"></span></span>
  </div>

  <h2 class="h2" style="left:43px;top:975px">For Franchisees</h2>
  <div class="copy" style="left:43px;top:1000px;width:193px">Lantern Petals brings the best of professional florists and supermarkets together for the benefit of consumers. It supports a national network of owner-operator franchisees, who in many cases are multi-site professional florists, with comprehensive services to enhance franchise profitability. Lantern Petals works with some of the country’s largest and most progressive supermarkets to provide franchisee ownership and operation of their strategically important floral departments.</div>
  <span class="btn" style="left:43px;top:1102px">LEARN MORE <span class="btn__arrow"></span></span>
  <div style="position:absolute;left:262px;top:964px;width:211px;height:184px;border-left:1.5px solid var(--orange);border-bottom:1.5px solid var(--green)"></div>
  <div class="photo" style="left:268px;top:958px;width:205px;height:182px;background:linear-gradient(135deg,#dfe3dc,#f2c2ae 45%,#fbeee6 65%,#7f9a78)" role="img" aria-label="Wrapped bouquet of white and peach roses"></div>

  <footer class="footer">
    <svg class="footer__wave" viewBox="0 0 473 80" preserveAspectRatio="none"><path fill="#f29b17" d="M0 50C150 -5 330 62 473 6V80H0Z"/><path fill="#129a4a" d="M0 58C150 3 330 70 473 14V80H0Z"/><path fill="#050505" d="M0 66C150 11 330 78 473 24V80H0Z"/></svg>
    <div class="footer__body">
      <div class="footer__brand"><span class="brand__dot"></span>Lantern Petals</div>
      <div class="footer__col footer__col--links"><h4>QUICK LINKS</h4><ul><li>Home</li><li>About</li><li>For Supermarkets</li><li>For Franchisees</li><li>Contact</li></ul></div>
      <div class="footer__col footer__col--contact"><h4>CONTACT US</h4><ul><li><span class="ic"></span><span class="footer__phone">+ 1.555.010.2040</span></li><li><span class="ic"></span>hello@lantern-petals.com</li><li><span class="ic"></span>114 Orchard Lane, Suite 2<br>Springfield, 55501</li><li><span class="ic"></span><span class="footer__loc">View Other Locations</span></li></ul></div>
      <div class="footer__col footer__col--news"><h4>SUBSCRIBE NOW</h4><p>Sign up to our newsletter and stay up to date</p><div class="signup">Email Address<span class="signup__go"></span></div><div class="footer__social"><span></span><span></span></div></div>
    </div>
    <div class="footer__bar">© 2024 Lantern Petals. All Rights Reserved</div>
  </footer>
</section>

<!-- ================= ABOUT ================= -->
<section class="page page--about">
  <header class="topbar">
    <div class="brand"><span class="brand__dot"></span>Lantern Petals</div>
    <span class="social social--a"></span><span class="social social--b"></span>
    <div class="call"><span class="call__icon"><svg width="7" height="7" viewBox="0 0 24 24"><path fill="#fff" d="M6.6 10.8a15 15 0 0 0 6.6 6.6l2.2-2.2c.3-.3.7-.4 1-.2 1.1.4 2.3.6 3.6.6.6 0 1 .4 1 1V20c0 .6-.4 1-1 1A17 17 0 0 1 3 4c0-.6.4-1 1-1h3.5c.6 0 1 .4 1 1 0 1.3.2 2.5.6 3.6.1.3 0 .7-.2 1z"/></svg></span><div class="call__text">Call Us<b>+ 1.555.010.2040</b></div></div>
    <nav class="nav"><span>HOME</span><span>ABOUT</span><span>FOR SUPERMARKETS</span><span>FOR FRANCHISEES</span><span>CONTACT</span></nav>
  </header>
  <div class="hero hero--about" role="img" aria-label="Florist holding a bouquet of peonies and roses">
    <div class="hero__shade"></div>
    <div class="hero__title hero__single">About Us</div>
  </div>
  <svg class="wave wave--hero" viewBox="0 0 473 105" preserveAspectRatio="none"><path fill="#f29b17" d="M0 46C120 -2 260 84 473 16V105H0Z"/><path fill="#129a4a" d="M0 60C120 12 260 98 473 30V105H0Z"/><path fill="#fff" d="M0 68C120 20 260 106 473 38V105H0Z"/></svg>

  <div class="copy" style="left:43px;top:374px;width:167px"><p>Fresh flowers convey beauty and love, and in our view should become something every person regularly enjoys. Lantern Petals is an entrepreneurial company created to make top quality fresh flowers and professionally-designed bouquets accessible to every consumer at affordable prices.</p><p>Professional florists typically sell the finest quality stems, design the most beautiful bouquets and provide the finest customer service, but their costs – of floral products, retail spaces, labor and marketing – force them to pass high prices along to customers. Supermarket flower departments benefit from high customer footfall, economies of scale and low pricing, but their quality of stems and bouquets is typically poor, staffing is limited, and staff turnover is high which can result in inefficiency, wastage, poorly merchandised selections and limited service.</p></div>
  <div class="hex" style="left:263px;top:362px;width:66px;height:74px;background:linear-gradient(135deg,#f1a6b8,#f6d7d0)" role="img" aria-label="Tulip bouquet"></div>
  <div class="hex" style="left:333px;top:362px;width:66px;height:74px;background:linear-gradient(135deg,#e88a1a,#f6b84a)" role="img" aria-label="Orange roses"></div>
  <div class="hex" style="left:228px;top:420px;width:66px;height:74px;background:linear-gradient(135deg,#7c5a4b,#d79fb1)" role="img" aria-label="Florist with flowers"></div>
  <div class="hex" style="left:298px;top:420px;width:66px;height:74px;background:linear-gradient(135deg,#e9502d,#f6c548)" role="img" aria-label="Bright mixed bouquet"></div>
  <div class="hex" style="left:368px;top:420px;width:66px;height:74px;background:linear-gradient(135deg,#5a2d5f,#c74f78)" role="img" aria-label="Dark purple flowers"></div>
  <div class="hex" style="left:263px;top:478px;width:66px;height:74px;background:linear-gradient(135deg,#d9781d,#f1a33a)" role="img" aria-label="Orange flower arrangement"></div>
  <div class="hex" style="left:333px;top:478px;width:66px;height:74px;background:linear-gradient(135deg,#d73a6c,#f38aa6)" role="img" aria-label="Pink gerberas"></div>

  <div class="frame" style="left:148px;top:603px;width:74px;height:175px;border-left:none;border-bottom:none"></div>
  <div class="frame" style="left:150px;top:640px;width:91px;height:118px;border-left:none;border-top:none"></div>
  <div class="photo" style="left:43px;top:582px;width:160px;height:140px;background:linear-gradient(135deg,#8c9aa0,#f2eee6 40%,#e9a4b5 65%,#6c8a5a)" role="img" aria-label="Supermarket flower display"></div>
  <div class="photo" style="left:148px;top:638px;width:91px;height:106px;border:2px solid #fff;background:linear-gradient(135deg,#b8c4c8,#e3d08a 60%,#6d8f5a)" role="img" aria-label="Florist standing beside sunflowers"></div>
  <div class="photo" style="left:100px;top:700px;width:64px;height:75px;border:2px solid #fff;background:#e8e2de;display:flex;align-items:center;justify-content:center" role="img" aria-label="Partner badge"><span style="width:22px;height:22px;border-radius:50%;background:#c59b5a"></span></div>
  <div class="copy" style="left:260px;top:580px;width:172px"><p>Lantern Petals brings the best of professional florists and supermarkets together for the benefit of consumers. It supports a national network of owner-operator franchisees, who in many cases are multi-site professional florists, with comprehensive services to enhance franchise profitability. Lantern Petals works with some of the country’s largest and most progressive supermarkets to provide franchisee ownership and operation of their strategically important floral departments. Supermarkets find that Lantern Petals is able to improve their financial outcomes, provide attentive customer service and satisfaction, and lift the quality of the entire store environment.</p><p>Lantern Petals operates in partnership with Bluegale Group, the leading franchisor of sushi stations and pre-packaged fruit &amp; vegetable departments to supermarkets across the United States and United Kingdom. Lantern Petals’ combination of floral and supermarket franchising expertise guarantees that consumers, franchisees and supermarket partners each receive exceptional service and value.</p></div>

  <footer class="footer">
    <svg class="footer__wave" viewBox="0 0 473 80" preserveAspectRatio="none"><path fill="#f29b17" d="M0 50C150 -5 330 62 473 6V80H0Z"/><path fill="#129a4a" d="M0 58C150 3 330 70 473 14V80H0Z"/><path fill="#050505" d="M0 66C150 11 330 78 473 24V80H0Z"/></svg>
    <div class="footer__body">
      <div class="footer__brand"><span class="brand__dot"></span>Lantern Petals</div>
      <div class="footer__col footer__col--links"><h4>QUICK LINKS</h4><ul><li>Home</li><li>About</li><li>For Supermarkets</li><li>For Franchisees</li><li>Contact</li></ul></div>
      <div class="footer__col footer__col--contact"><h4>CONTACT US</h4><ul><li><span class="ic"></span><span class="footer__phone">+ 1.555.010.2040</span></li><li><span class="ic"></span>hello@lantern-petals.com</li><li><span class="ic"></span>114 Orchard Lane, Suite 2<br>Springfield, 55501</li><li><span class="ic"></span><span class="footer__loc">View Other Locations</span></li></ul></div>
      <div class="footer__col footer__col--news"><h4>SUBSCRIBE NOW</h4><p>Sign up to our newsletter and stay up to date</p><div class="signup">Email Address<span class="signup__go"></span></div><div class="footer__social"><span></span><span></span></div></div>
    </div>
    <div class="footer__bar">© 2024 Lantern Petals. All Rights Reserved</div>
  </footer>
</section>

<!-- ================= SUPERMARKETS ================= -->
<section class="page page--markets">
  <header class="topbar">
    <div class="brand"><span class="brand__dot"></span>Lantern Petals</div>
    <span class="social social--a"></span><span class="social social--b"></span>
    <div class="call"><span class="call__icon"><svg width="7" height="7" viewBox="0 0 24 24"><path fill="#fff" d="M6.6 10.8a15 15 0 0 0 6.6 6.6l2.2-2.2c.3-.3.7-.4 1-.2 1.1.4 2.3.6 3.6.6.6 0 1 .4 1 1V20c0 .6-.4 1-1 1A17 17 0 0 1 3 4c0-.6.4-1 1-1h3.5c.6 0 1 .4 1 1 0 1.3.2 2.5.6 3.6.1.3 0 .7-.2 1z"/></svg></span><div class="call__text">Call Us<b>+ 1.555.010.2040</b></div></div>
    <nav class="nav"><span>HOME</span><span>ABOUT</span><span>FOR SUPERMARKETS</span><span>FOR FRANCHISEES</span><span>CONTACT</span></nav>
  </header>
  <div class="hero hero--markets" role="img" aria-label="Florist carrying a basket of roses in a flower shop">
    <div class="hero__shade"></div>
    <div class="hero__title hero__single">Supermarkets</div>
  </div>
  <svg class="wave wave--hero" viewBox="0 0 473 105" preserveAspectRatio="none"><path fill="#f29b17" d="M0 46C120 -2 260 84 473 16V105H0Z"/><path fill="#129a4a" d="M0 60C120 12 260 98 473 30V105H0Z"/><path fill="#fff" d="M0 68C120 20 260 106 473 38V105H0Z"/></svg>

  <div class="copy copy--center" style="left:45px;top:383px;width:383px">Lantern Petals works with some of the country’s largest and most progressive supermarkets to provide franchisee ownership and operation of their strategically important floral departments. Supermarkets find that Lantern Petals is able to improve their financial outcomes, provide attentive customer service and satisfaction, and lift the quality of the entire store environment.</div>
  <h2 class="h2 h2--center" style="top:423px">Opportunity for Supermarkets</h2>
  <div class="hex" style="left:53px;top:455px;width:144px;height:160px;background:var(--green)"></div>
  <div class="hex" style="left:57px;top:460px;width:136px;height:150px;background:linear-gradient(135deg,#c7cfc8,#b99a7a 50%,#d7687a)" role="img" aria-label="Florist preparing a bouquet at a counter"></div>
  <ul class="list" style="left:230px;top:472px;width:200px">
    <li>Enhance floral revenue streams with efficient assortments and new offerings</li>
    <li>Reduce the costs of operating a floral department</li>
    <li>Improve the quality, useful life and merchandising of floral products</li>
    <li>Provide attentive customer service, including semi-custom bouquets, by professional florist staff</li>
    <li>Maintain a beautiful, fresh and well-stocked environment</li>
    <li>Increase sales and profits</li>
    <li>Enhance the entire customer shopping environment</li>
  </ul>
  <div class="copy" style="left:41px;top:650px;width:191px">Lantern Petals operates in partnership with Bluegale Group, a leading international, multi-channel Japanese food business and the largest franchisor of sushi stations and pre-packaged fruit and vegetable departments to supermarkets across the United States, Canada and the United Kingdom. Bluegale, working closely with its supermarket partners, has recognised that franchising select supermarket food departments beyond sushi can dramatically improve financial performance for the supermarkets while creating entrepreneurial business opportunities for franchisees. It has chosen to support Lantern Petals in assisting supermarkets with a similarly compelling opportunity in floral departments. Lantern Petals’ combination of floral and supermarket franchising expertise guarantees that consumers, franchisees and supermarket partners each receive exceptional service and value.</div>
  <div class="photo" style="left:258px;top:616px;width:176px;height:235px;background:linear-gradient(165deg,#f3c36a 0%,#f7e2b8 45%,#dcefe1 100%)" role="img" aria-label="Illustration of a bee, honeycomb and a growing flower stem"></div>

  <footer class="footer">
    <svg class="footer__wave" viewBox="0 0 473 80" preserveAspectRatio="none"><path fill="#f29b17" d="M0 50C150 -5 330 62 473 6V80H0Z"/><path fill="#129a4a" d="M0 58C150 3 330 70 473 14V80H0Z"/><path fill="#050505" d="M0 66C150 11 330 78 473 24V80H0Z"/></svg>
    <div class="footer__body">
      <div class="footer__brand"><span class="brand__dot"></span>Lantern Petals</div>
      <div class="footer__col footer__col--links"><h4>QUICK LINKS</h4><ul><li>Home</li><li>About</li><li>For Supermarkets</li><li>For Franchisees</li><li>Contact</li></ul></div>
      <div class="footer__col footer__col--contact"><h4>CONTACT US</h4><ul><li><span class="ic"></span><span class="footer__phone">+ 1.555.010.2040</span></li><li><span class="ic"></span>hello@lantern-petals.com</li><li><span class="ic"></span>114 Orchard Lane, Suite 2<br>Springfield, 55501</li><li><span class="ic"></span><span class="footer__loc">View Other Locations</span></li></ul></div>
      <div class="footer__col footer__col--news"><h4>SUBSCRIBE NOW</h4><p>Sign up to our newsletter and stay up to date</p><div class="signup">Email Address<span class="signup__go"></span></div><div class="footer__social"><span></span><span></span></div></div>
    </div>
    <div class="footer__bar">© 2024 Lantern Petals. All Rights Reserved</div>
  </footer>
</section>

<!-- ================= FRANCHISEES ================= -->
<section class="page page--franchise">
  <header class="topbar">
    <div class="brand"><span class="brand__dot"></span>Lantern Petals</div>
    <span class="social social--a"></span><span class="social social--b"></span>
    <div class="call"><span class="call__icon"><svg width="7" height="7" viewBox="0 0 24 24"><path fill="#fff" d="M6.6 10.8a15 15 0 0 0 6.6 6.6l2.2-2.2c.3-.3.7-.4 1-.2 1.1.4 2.3.6 3.6.6.6 0 1 .4 1 1V20c0 .6-.4 1-1 1A17 17 0 0 1 3 4c0-.6.4-1 1-1h3.5c.6 0 1 .4 1 1 0 1.3.2 2.5.6 3.6.1.3 0 .7-.2 1z"/></svg></span><div class="call__text">Call Us<b>+ 1.555.010.2040</b></div></div>
    <nav class="nav"><span>HOME</span><span>ABOUT</span><span>FOR SUPERMARKETS</span><span>FOR FRANCHISEES</span><span>CONTACT</span></nav>
  </header>
  <div class="hero hero--franchise" role="img" aria-label="Florist holding a large purple and white bouquet">
    <div class="hero__shade"></div>
    <div class="hero__title hero__single">Franchisees</div>
  </div>
  <svg class="wave wave--hero" viewBox="0 0 473 105" preserveAspectRatio="none"><path fill="#f29b17" d="M0 46C120 -2 260 84 473 16V105H0Z"/><path fill="#129a4a" d="M0 60C120 12 260 98 473 30V105H0Z"/><path fill="#fff" d="M0 68C120 20 260 106 473 38V105H0Z"/></svg>

  <div class="photo" style="left:43px;top:379px;width:153px;height:107px;background:linear-gradient(180deg,#6f7f8a,#b9c2c4 30%,#a0503f 60%,#3f6b3f)" role="img" aria-label="Greenhouse with rows of red flowers"></div>
  <div class="copy" style="left:240px;top:384px;width:190px">Lantern Petals brings the best of professional florists and supermarkets together for the benefit of consumers. It supports a national network of owner-operator franchisees, who in many cases are multi-site professional florists, with comprehensive services to enhance franchise profitability. Lantern Petals works with some of the country’s largest and most progressive supermarkets to provide franchisee ownership and operation of their strategically important floral departments.</div>
  <h2 class="h2 h2--center" style="top:517px">Opportunity for New Florist Franchisees</h2>
  <ul class="list" style="left:43px;top:566px;width:175px">
    <li>Be an owner, and your own boss</li>
    <li>Attractive earnings potential; paid weekly</li>
    <li>No experience necessary, we set you up to operate and provide extensive support</li>
    <li>Professional training provided, and a path to floral design industry certification</li>
    <li>Low operating and supply costs which leverage supermarket</li>
    <li>Affordable franchise fees and low initial investment</li>
    <li>Opportunities to expand to different locations</li>
  </ul>
  <div class="frame" style="left:255px;top:562px;width:175px;height:126px;border-width:2px;border-radius:3px"></div>
  <div class="photo" style="left:258px;top:565px;width:169px;height:120px;background:linear-gradient(135deg,#a7b7b0,#d8c2a6 45%,#c94f6e 70%,#5d8a4e)" role="img" aria-label="Smiling florist arranging flowers"></div>
  <h2 class="h2 h2--center" style="top:722px">Opportunity for Professional Floral Retailers</h2>
  <div class="frame" style="left:50px;top:762px;width:176px;height:128px;border-width:2px;border-color:#f29b17 var(--green) var(--green) #f29b17"></div>
  <div class="photo" style="left:53px;top:765px;width:170px;height:122px;background:linear-gradient(135deg,#e8c3c9,#f4a0b8 40%,#fbe9e6 60%,#c59a8a)" role="img" aria-label="Pink floral arrangement"></div>
  <ul class="list" style="left:250px;top:781px;width:182px">
    <li>Become a multi-site florist</li>
    <li>Add a high volume, high traffic location</li>
    <li>Enhance customer acquisition for specialty custom events</li>
    <li>Reduce product costs</li>
    <li>Leverage staffing across locations</li>
    <li>Leverage Lantern Petals best-in-class technology, support and marketing across locations</li>
  </ul>

  <footer class="footer">
    <svg class="footer__wave" viewBox="0 0 473 80" preserveAspectRatio="none"><path fill="#f29b17" d="M0 50C150 -5 330 62 473 6V80H0Z"/><path fill="#129a4a" d="M0 58C150 3 330 70 473 14V80H0Z"/><path fill="#050505" d="M0 66C150 11 330 78 473 24V80H0Z"/></svg>
    <div class="footer__body">
      <div class="footer__brand"><span class="brand__dot"></span>Lantern Petals</div>
      <div class="footer__col footer__col--links"><h4>QUICK LINKS</h4><ul><li>Home</li><li>About</li><li>For Supermarkets</li><li>For Franchisees</li><li>Contact</li></ul></div>
      <div class="footer__col footer__col--contact"><h4>CONTACT US</h4><ul><li><span class="ic"></span><span class="footer__phone">+ 1.555.010.2040</span></li><li><span class="ic"></span>hello@lantern-petals.com</li><li><span class="ic"></span>114 Orchard Lane, Suite 2<br>Springfield, 55501</li><li><span class="ic"></span><span class="footer__loc">View Other Locations</span></li></ul></div>
      <div class="footer__col footer__col--news"><h4>SUBSCRIBE NOW</h4><p>Sign up to our newsletter and stay up to date</p><div class="signup">Email Address<span class="signup__go"></span></div><div class="footer__social"><span></span><span></span></div></div>
    </div>
    <div class="footer__bar">© 2024 Lantern Petals. All Rights Reserved</div>
  </footer>
</section>

</div>
</body>
</html>
```